Vindgerdi - Start-up company selling electricity

Hello let me tell you about Vindgerdi.

Vindgerdi is start-up company selling electricity in Iceland. The operations of the company consist of making power usage forecasts for our customers, purchasing the electricity wholesale from the energy producers, and selling the electricity to the consumer. We are focused on tech by using optimization and machine learning to minimize electricity prices to our customers. Our marketing strategy is to portray a tech company mindset and to show dedication to driving down the electricity price on the market.

We need your help to make our website pop. Possible concepts to work with are as follows:

- Iceland the land of ice and fire
- Green energy
- Innovation
- Tech and data science

Link to our website: https://prufa.vindgerdi-example.is/
We are open to ideas.
Thank you!

Target Market(s)

Electricity consumers both homes and companies.

Number of Pages Required

1 page

Font styles to use
Serif
Sans Serif

```html
<!DOCTYPE html>
<html lang="en">
<head>
<meta charset="utf-8">
<title>Vindgerdi – Same electricity, just cheaper</title>
<link href="https://fonts.googleapis.com/css2?family=Lora:wght@400;700&family=Roboto:wght@400;500;700&family=Lato:wght@400;700&display=swap" rel="stylesheet">
<style>
:root{
  --red:#9b2a22;
  --red-dark:#7d1f19;
  --navy:#1c3461;
  --navy-soft:rgba(28,52,97,.88);
  --ink:#1b1b1b;
  --muted:#666;
  --line:#e6e6e6;
  --footer:#232323;
  --white:#fff;
}
*{box-sizing:border-box;margin:0;padding:0}
html,body{width:1200px;height:2981px;overflow:hidden}
body{position:relative;font-family:'Roboto',sans-serif;color:var(--ink);background:var(--white)}
.btn{position:absolute;display:flex;align-items:center;justify-content:center;gap:10px;color:var(--white);font:700 14px 'Roboto',sans-serif;letter-spacing:.4px;border-radius:3px;text-transform:uppercase;text-decoration:none}
.btn-red{background:var(--red)}
.btn-navy{background:var(--navy)}
.btn svg{width:14px;height:14px}

/* header */
.site-header{position:absolute;left:0;top:0;width:1200px;height:87px;background:var(--white)}
.brand{position:absolute;left:112px;top:28px;display:flex;align-items:center;gap:10px}
.brand-dot{width:22px;height:22px;border-radius:50%;background:var(--navy)}
.brand-name{font:400 26px 'Lora',serif;color:var(--red);letter-spacing:.5px}
.main-nav a{position:absolute;top:35px;font:500 14px 'Roboto',sans-serif;color:var(--ink);letter-spacing:.6px;text-decoration:none}

/* hero */
.hero{position:absolute;left:0;top:87px;width:1200px;height:557px;background:linear-gradient(180deg,#8a96a1 0%,#b5bcc0 30%,#7d8660 55%,#4f5436 75%,#3b3f34 100%)}
.hero-title{position:absolute;left:0;width:1200px;top:76px;text-align:center;font:700 80px/90px 'Lora',serif;color:var(--white);letter-spacing:2px}
.hero-sub{position:absolute;left:300px;width:600px;top:172px;text-align:center;color:#f4f4f4;font:400 19px/30px 'Roboto',sans-serif}
.arrow{position:absolute;width:40px;height:40px;border-radius:50%;background:var(--white);display:flex;align-items:center;justify-content:center}

/* about */
.about-photo{position:absolute;left:210px;top:860px;width:320px;height:360px;border-radius:50%;background:radial-gradient(circle at 50% 65%,#2bb2dc 0%,#7fcde6 40%,#dbeaf1 70%,#eef3f6 100%);box-shadow:8px 10px 0 #e4e4e4}
.about-title{position:absolute;left:628px;top:730px;font:700 46px 'Lora',serif}
.about-q{position:absolute;left:628px;top:798px;width:480px;font:500 18px/27px 'Roboto',sans-serif;letter-spacing:.5px}
.about-text{position:absolute;left:628px;top:862px;width:465px;font:400 14.5px/29px 'Roboto',sans-serif;color:var(--muted)}

.divider{position:absolute;left:0;top:1298px;width:1200px;height:1px;background:var(--line)}

/* features */
.section-title{position:absolute;left:0;width:1200px;top:1370px;text-align:center;font:700 41px 'Lora',serif;letter-spacing:.5px}
.feature{position:absolute;top:1486px;width:340px;text-align:center}
.feature-icon{margin:0 auto;width:108px;height:108px;border-radius:50%;border:2px solid;display:flex;align-items:center;justify-content:center;background:var(--white)}
.feature-icon span{width:92px;height:92px;border-radius:50%;display:flex;align-items:center;justify-content:center}
.feature h3{margin-top:28px;font:500 17px 'Roboto',sans-serif;letter-spacing:.6px}
.feature .bar{margin:14px auto 0;width:34px;height:2px;background:var(--red)}
.feature p{margin-top:17px;font:400 14px/25.5px 'Roboto',sans-serif;color:var(--muted)}
.feature p.tight{line-height:21px}
.prices{display:flex;justify-content:center;gap:34px;margin-top:6px}
.price b{display:block;font:500 26px 'Roboto',sans-serif}
.price small{font:400 14px 'Roboto',sans-serif;color:var(--muted)}

/* Q&A */
.qa{position:absolute;left:0;top:1903px;width:1200px;height:666px;background:linear-gradient(180deg,#5f83ad 0%,#9bb6cf 35%,#e1e9ef 55%,#2e86b8 72%,#0d4e85 88%,#c9d8e3 100%)}
.qa-accent{position:absolute;left:746px;top:2090px;width:318px;height:390px;border-radius:50%;background:rgba(255,255,255,.28)}
.qa-title{position:absolute;left:119px;top:1990px;font:400 42px 'Lora',serif;color:var(--white)}
.acc{position:absolute;left:120px;width:522px;height:61px;background:var(--navy-soft);display:flex;align-items:center}
.acc .toggle{width:62px;height:100%;background:var(--navy);color:var(--white);display:flex;align-items:center;justify-content:center;font:700 24px 'Lato',sans-serif}
.acc .q{padding-left:38px;color:var(--white);font:700 14.5px 'Lato',sans-serif}
.acc-body{position:absolute;left:120px;top:2135px;width:522px;height:115px;background:var(--white);display:flex;align-items:center;gap:24px;padding-left:14px}
.acc-thumb{width:106px;height:84px;background:linear-gradient(180deg,#8fa9c4 0%,#6c7c8a 50%,#2c3a22 100%)}
.acc-body p{font:400 15px/22px 'Lato',sans-serif;color:#555;width:330px}

/* footer */
.site-footer{position:absolute;left:0;top:2569px;width:1200px;height:412px;background:var(--footer);color:var(--white)}
.f-head{position:absolute;font:500 14px 'Roboto',sans-serif;letter-spacing:.3px}
.field{position:absolute;background:var(--white);color:#777;font:400 14px 'Roboto',sans-serif;padding:12px 9px;border:1px solid #ccc}
.info{position:absolute;left:628px;display:flex;gap:18px;align-items:flex-start;font:400 14.5px/26px 'Roboto',sans-serif;color:#eee}
.info i{width:30px;height:30px;border-radius:50%;background:var(--white);display:flex;align-items:center;justify-content:center;flex:none}
.links a{position:absolute;left:953px;color:#eee;font:400 14.5px 'Roboto',sans-serif;text-decoration:none;display:flex;gap:14px;align-items:center}
.social{position:absolute;top:2810px;width:28px;height:28px;border-radius:50%}
.foot-rule{position:absolute;left:112px;top:2902px;width:976px;height:1px;background:#444}
.legal{position:absolute;top:2926px;font:400 13.5px 'Roboto',sans-serif;color:#eee}
</style>
</head>
<body>

<header class="site-header">
  <div class="brand"><span class="brand-dot"></span><span class="brand-name">VINDGERDI</span></div>
  <nav class="main-nav">
    <a style="left:378px">TERMS OF BUSINESS</a>
    <a style="left:557px">QUESTION &amp; ANSWER</a>
    <a style="left:741px">ABOUT VINDGERDI</a>
  </nav>
  <a class="btn btn-red" style="left:931px;top:19px;width:157px;height:50px">Get Started
    <svg viewBox="0 0 16 16"><circle cx="8" cy="8" r="7" fill="#fff"/><path d="M6 4.5 9.5 8 6 11.5" stroke="#9b2a22" stroke-width="2" fill="none"/></svg></a>
</header>

<section class="hero" role="img" aria-label="Technician in a hard hat sitting on a wind turbine above green fields with turbines behind">
  <h1 class="hero-title">VINDGERDI</h1>
  <p class="hero-sub">Vindgerdi uses automation and artificial intelligence to achieve<br>lower prices in the electricity market.</p>
  <a class="btn btn-red" style="left:522px;top:252px;width:156px;height:51px">Get Started
    <svg viewBox="0 0 16 16"><circle cx="8" cy="8" r="7" fill="#fff"/><path d="M6 4.5 9.5 8 6 11.5" stroke="#9b2a22" stroke-width="2" fill="none"/></svg></a>
  <span class="arrow" style="left:37px;top:259px"><svg width="14" height="14" viewBox="0 0 14 14"><path d="M9 2 4 7l5 5" stroke="#111" stroke-width="2" fill="none"/></svg></span>
  <span class="arrow" style="left:1123px;top:259px"><svg width="14" height="14" viewBox="0 0 14 14"><path d="M5 2l5 5-5 5" stroke="#111" stroke-width="2" fill="none"/></svg></span>
</section>

<section class="about">
  <div class="about-photo" role="img" aria-label="Icy glacier lagoon with turquoise water and snowy mountains"></div>
  <h2 class="about-title"><span style="color:var(--red)">ABOUT</span> <span style="color:var(--navy)">US</span></h2>
  <h3 class="about-q">WHAT IS VINDGERDI'S UNIQUE POSITION IN THE ELECTRICITY SALES MARKET?</h3>
  <p class="about-text">Vindgerdi uses automation and artificial intelligence to achieve lower prices in the electricity market. Our goal is to minimize the cost of energy sales, promote energy balance and offer good service. Vindgerdi's goal is to offer its customers the most favorable electricity prices in Iceland. Electricity is part of the monthly costs of households and companies, and by doing business with Vindgerdi, savings can be achieved and operating costs reduced. Vindgerdi wants to make the electricity system "smarter". Data science and the use of artificial intelligence can maximize</p>
  <a class="btn btn-red" style="left:628px;top:1145px;width:156px;height:50px">Learn More
    <svg viewBox="0 0 16 16"><circle cx="8" cy="8" r="7" fill="#fff"/><path d="M6 4.5 9.5 8 6 11.5" stroke="#9b2a22" stroke-width="2" fill="none"/></svg></a>
</section>

<div class="divider"></div>

<section class="features">
  <h2 class="section-title"><span style="color:var(--red)">SAME ELECTRICITY</span>&nbsp; <span style="color:var(--navy)">JUST CHEAPER</span></h2>

  <div class="feature" style="left:89px">
    <div class="feature-icon" style="border-color:var(--red)"><span style="background:radial-gradient(circle,#b3342a,#6e1712)">
      <svg width="44" height="44" viewBox="0 0 44 44" fill="none" stroke="#fff" stroke-width="1.6"><circle cx="22" cy="14" r="8"/><circle cx="22" cy="14" r="3"/><path d="M6 30l10-6 8 4 10-4 4 8-14 8H12z"/></svg></span></div>
    <h3>WELCOME TO BUSINESS</h3><div class="bar"></div>
    <p class="tight">The business terms only apply to the sale of<br>electricity and not to the production,</p>
  </div>
  <a class="btn btn-red" style="left:134px;top:1726px;width:118px;height:38px">Company</a>
  <a class="btn btn-navy" style="left:270px;top:1726px;width:118px;height:38px">Home</a>

  <div class="feature" style="left:429px">
    <div class="feature-icon" style="border-color:var(--navy)"><span style="background:radial-gradient(circle,#2b467a,#0f1e3c)">
      <svg width="44" height="44" viewBox="0 0 44 44" fill="none" stroke="#fff" stroke-width="1.6"><path d="M24 6h14v14L20 38 6 24z"/><circle cx="32" cy="12" r="2"/><path d="M18 20c2-2 6 0 4 3s2 5 4 3"/></svg></span></div>
    <h3>PRICE LIST</h3><div class="bar"></div>
    <p>Make a price comparison</p>
    <div class="prices">
      <div class="price"><b style="color:var(--red)">6.95</b><small>ISK / kWh</small></div>
      <div class="price"><b style="color:var(--navy)">6.22</b><small>ISK / kWh</small></div>
    </div>
    <p style="margin-top:12px">electric acceleration</p>
  </div>

  <div class="feature" style="left:768px">
    <div class="feature-icon" style="border-color:var(--red)"><span style="background:radial-gradient(circle,#b3342a,#6e1712)">
      <svg width="44" height="44" viewBox="0 0 44 44" fill="none" stroke="#fff" stroke-width="1.6"><circle cx="22" cy="18" r="9"/><path d="M8 6v14l6 8M36 6v14l-6 8M14 34h16v6H14z"/></svg></span></div>
    <h3>THE FUTURE IS EXCITING</h3><div class="bar"></div>
    <p>Let's make the electricity system<br>smarter together. Vindgerdi uses artificial<br>intelligence, data science and automation to<br>minimize costs and promote eccentricity</p>
  </div>
</section>

<section class="qa" role="img" aria-label="Snowy Icelandic landscape with a blue meltwater lake under a cloudy sky"></section>
<div class="qa-accent"></div>
<h2 class="qa-title">QUESTION &amp; ANSWER</h2>
<div class="acc" style="top:2074px"><span class="toggle">–</span><span class="q">CAN ANYONE BUY ELECTRICITY FROM VINDGERDI ?</span></div>
<div class="acc-body"><div class="acc-thumb" role="img" aria-label="Mountain ridge under a blue sky"></div><p>Yes! Everyone in Iceland can buy electricity from Vindgerdi</p></div>
<div class="acc" style="top:2269px"><span class="toggle">+</span><span class="q">NEMO ENIM IPSAM VOLUPTATEM QUIA VOLUPTAS ?</span></div>
<div class="acc" style="top:2344px"><span class="toggle">+</span><span class="q">NEMO ENIM IPSAM VOLUPTATEM QUIA VOLUPTAS ?</span></div>
<div class="acc" style="top:2420px"><span class="toggle">+</span><span class="q">NEMO ENIM IPSAM VOLUPTATEM QUIA VOLUPTAS ?</span></div>

<footer class="site-footer"></footer>
<h4 class="f-head" style="left:112px;top:2602px;color:#fff;font-size:16px">CONTACT FORM</h4>
<div class="field" style="left:112px;top:2643px;width:222px;height:45px">First Name</div>
<div class="field" style="left:345px;top:2643px;width:222px;height:45px">Last Name</div>
<div class="field" style="left:112px;top:2695px;width:222px;height:44px">Email</div>
<div class="field" style="left:345px;top:2695px;width:222px;height:44px">Phone No</div>
<div class="field" style="left:112px;top:2748px;width:456px;height:76px">Message</div>
<a class="btn btn-red" style="left:112px;top:2835px;width:117px;height:45px">Submit</a>

<h4 class="f-head" style="left:628px;top:2605px;color:#fff">CONTACT INFO</h4>
<div class="info" style="top:2633px"><i><svg width="14" height="14" viewBox="0 0 14 14"><path d="M7 13s5-5 5-8a5 5 0 0 0-10 0c0 3 5 8 5 8z" fill="#232323"/><circle cx="7" cy="5" r="1.8" fill="#fff"/></svg></i><span>Fjordur Hall Level 6,<br>Harbour island</span></div>
<div class="info" style="top:2700px"><i><svg width="14" height="14" viewBox="0 0 14 14"><path d="M3 1l3 3-1.5 2a8 8 0 0 0 3.5 3.5L10 8l3 3-2 2C6 13 1 8 1 3z" fill="#232323"/></svg></i><span>1 555 010 019</span></div>
<div class="info" style="top:2750px"><i><svg width="14" height="14" viewBox="0 0 14 14"><rect x="1.5" y="3" width="11" height="8" rx="1" fill="none" stroke="#232323" stroke-width="1.4"/><path d="M1.5 3.5 7 8l5.5-4.5" fill="none" stroke="#232323" stroke-width="1.4"/></svg></i><span>info@vindgerdi-example.is</span></div>
<h4 class="f-head" style="left:628px;top:2815px;color:#fff;font-size:16px">STAY CONNECTED</h4>
<span class="social" style="left:804px;background:#3b5998"></span>
<span class="social" style="left:842px;background:#1da1f2"></span>
<span class="social" style="left:880px;background:#dd4b39"></span>
<span class="social" style="left:918px;background:#0e76a8"></span>
<span class="social" style="left:956px;background:#e52d27"></span>

<h4 class="f-head" style="left:953px;top:2605px;color:#fff">QUICK LINKS</h4>
<nav class="links">
  <a style="top:2638px">»&nbsp; Home</a>
  <a style="top:2672px">»&nbsp; About Us</a>
  <a style="top:2706px">»&nbsp; FAQ</a>
  <a style="top:2740px">»&nbsp; Contact Us</a>
  <a style="top:2775px">»&nbsp; Terms Of Business</a>
</nav>
<div class="foot-rule"></div>
<p class="legal" style="left:112px">© 2021 Vindgerdi. All Rights reserved</p>
<p class="legal" style="left:908px">Terms Of Use &nbsp;|&nbsp; Privacy Policy</p>

</body>
</html>
```